Copperleaf Roofing Business Card

This is my current business card. But I’d like to make some changes. Somewhere on the card I’d like to list some of the services we offer. Maybe on the back? But I’d still like to keep the red. White and black modern look.

-residential & commercial roofing
-Roof Repairs & Maintenance
-Storm Damage & Insurance Claims specialist
-Christmas Lights and permanent Christmas lights
Fencing. Windows. Gutters. Siding. Sheetrock, painting.

```html
<!DOCTYPE html>
<html lang="en">
<head>
<meta charset="utf-8">
<title>Copperleaf Roofing Business Card</title>
<link href="https://fonts.googleapis.com/css2?family=Audiowide&family=Montserrat:wght@400;500&display=swap" rel="stylesheet">
<style>
  :root {
    --bg: #d4d5d7;
    --red: #e0232a;
    --red-dark: #6b0f12;
    --red-mid: #a8161c;
    --black: #111111;
    --white: #ffffff;
    --text: #1c1c1c;
  }
  * { margin: 0; padding: 0; box-sizing: border-box; }
  html, body { width: 900px; height: 1200px; overflow: hidden; }
  body { background: var(--bg); font-family: "Montserrat", sans-serif; position: relative; }

  .card {
    position: absolute;
    left: 120px;
    width: 660px;
    height: 376px;
    border-radius: 14px;
    overflow: hidden;
  }
  .card--front { top: 204px; }
  .card--back { top: 620px; background: var(--white); }

  .front-pattern {
    position: absolute; inset: 0;
    background: linear-gradient(180deg, var(--red-dark) 0%, var(--red) 30%, var(--red-mid) 55%, #2a0506 68%, var(--red) 82%, var(--red-dark) 100%);
  }
  .front-mark {
    position: absolute; left: 253px; top: 75px;
    width: 154px; height: 154px; border-radius: 50%;
    background: var(--black); border: 5px solid var(--white);
  }
  .front-name {
    position: absolute; left: 0; right: 0; top: 240px;
    text-align: center; color: var(--white);
    font-family: "Audiowide", sans-serif; font-weight: 400; line-height: 1.05;
  }
  .front-name .line1 { display: block; font-size: 40px; }
  .front-name .line2 { display: block; font-size: 26px; }

  .back-faint {
    position: absolute; left: 372px; top: 86px;
    width: 290px; height: 290px; border-radius: 50%;
    background: #f3eeee;
  }
  .back-mark {
    position: absolute; left: 87px; top: 25px;
    width: 116px; height: 116px; border-radius: 50%;
    background: var(--red);
  }
  .back-name {
    position: absolute; left: 28px; top: 152px; width: 240px;
    text-align: center; color: var(--red);
    font-family: "Audiowide", sans-serif; font-weight: 400; line-height: 1.1;
  }
  .back-name .line1 { display: block; font-size: 29px; }
  .back-name .line2 { display: block; font-size: 19px; }

  .person { position: absolute; left: 36px; top: 232px; }
  .person-name { font-family: "Audiowide", sans-serif; font-size: 25px; color: var(--black); letter-spacing: 0.5px; }
  .person-name .surname { color: var(--red); }
  .person-role { font-size: 14px; color: var(--text); margin-top: 2px; }

  .contacts { position: absolute; left: 38px; top: 293px; list-style: none; }
  .contacts li { display: flex; align-items: center; gap: 8px; font-size: 14.5px; color: var(--text); height: 24px; }
  .contacts svg { width: 14px; height: 14px; fill: var(--red); flex: none; }

  .services { position: absolute; right: 20px; top: 236px; list-style: none; text-align: right; }
  .services li { font-size: 14px; line-height: 16.5px; color: var(--text); margin-bottom: 6px; position: relative; padding-right: 12px; }
  .services li::after {
    content: ""; position: absolute; right: 0; top: 50%;
    width: 5px; height: 5px; border-radius: 50%; background: var(--red);
  }

  .back-band {
    position: absolute; left: 0; right: 0; bottom: 0; height: 12px;
    background: linear-gradient(90deg, var(--red-dark), var(--red), var(--red-dark), var(--red), var(--red-dark));
  }
</style>
</head>
<body>
  <section class="card card--front">
    <div class="front-pattern" role="img" aria-label="Red, black and white tartan plaid background"></div>
    <div class="front-mark"></div>
    <div class="front-name"><span class="line1">COPPERLEAF</span><span class="line2">ROOFING CO.</span></div>
  </section>

  <section class="card card--back">
    <div class="back-faint"></div>
    <div class="back-mark"></div>
    <div class="back-name"><span class="line1">COPPERLEAF</span><span class="line2">ROOFING CO.</span></div>

    <div class="person">
      <div class="person-name">DANA <span class="surname">WHITFIELD</span></div>
      <div class="person-role">Owner</div>
    </div>

    <ul class="contacts">
      <li><svg viewBox="0 0 24 24"><path d="M6.6 10.8a15.1 15.1 0 0 0 6.6 6.6l2.2-2.2a1 1 0 0 1 1-.25 11.4 11.4 0 0 0 3.6.57 1 1 0 0 1 1 1V20a1 1 0 0 1-1 1A17 17 0 0 1 3 4a1 1 0 0 1 1-1h3.5a1 1 0 0 1 1 1c0 1.25.2 2.45.57 3.57a1 1 0 0 1-.25 1z"/></svg>682-555-0148</li>
      <li><svg viewBox="0 0 24 24"><path d="M2 5h20v2l-10 6L2 7z M2 9l10 6 10-6v10H2z"/></svg>dana@copperleafroofing.com</li>
      <li><svg viewBox="0 0 24 24"><path d="M12 2a10 10 0 1 0 0 20 10 10 0 0 0 0-20zm0 2c1 1.3 1.8 3.2 2 5h-4c.2-1.8 1-3.7 2-5zM4.3 13h3.7c.1 1.9.6 3.7 1.4 5.2A8 8 0 0 1 4.3 13zm0-2a8 8 0 0 1 5.1-5.2C8.6 7.3 8.1 9.1 8 11zm7.7 9c-1-1.3-1.8-3.2-2-5h4c-.2 1.8-1 3.7-2 5zm2.6-1.8c.8-1.5 1.3-3.3 1.4-5.2h3.7a8 8 0 0 1-5.1 5.2zM16 11c-.1-1.9-.6-3.7-1.4-5.2A8 8 0 0 1 19.7 11z"/></svg>www.copperleafroofing.com</li>
    </ul>

    <ul class="services">
      <li>residential &amp; commercial roofing</li>
      <li>Roof Repairs &amp; Maintenance</li>
      <li>Storm Damage &amp;<br>Insurance Claims specialist</li>
      <li>Fencing. Windows. Gutters.<br>Siding. Sheetrock, painting</li>
    </ul>

    <div class="back-band" role="img" aria-label="Narrow strip of red tartan plaid"></div>
  </section>
</body>
</html>
```